Stationery Design Project

I need a stationary design for our company. we are based in Houston, TX and we are called Mira Vell Lending. And we are wanting to brand our MoneyMendPlus program, which includes our tax preparation and restoration, credit repair service. Although our business offers other programs, we are interested in mainly focusing on The MoneyMendPlus program. We are looking for way to brand our ourselves and I believe that a great stationery design will help in achieving this goal. Our logo design is blue and light blue. the slogan is orange.

Industry/Entity Type

Business

Requirements
Must have
• Address: 30871 Calloway Ln. B-22
Houston, TX 75419
Tel. 555-318-6207
Fax 555-294-7153
www.miravelllending.example
info@miravelllending.example
Our Slogan: Balance, Renewed!

```html
<!DOCTYPE html>
<html lang="en">
<head>
<meta charset="utf-8">
<title>MoneyMendPlus – Business Card</title>
<link rel="stylesheet" href="https://fonts.googleapis.com/css2?family=Tinos:wght@400;700&family=Jost:wght@400&display=swap">
<style>
  :root {
    --backdrop: #e9e6e2;
    --card-white: #ffffff;
    --brand-blue: #1a6fa8;
    --brand-navy: #0d3f6d;
    --brand-sky: #2a9bd8;
    --slogan-orange: #f29a1f;
    --ink: #1e1e1e;
    --faint-white: rgba(255, 255, 255, 0.22);
  }
  * { box-sizing: border-box; margin: 0; padding: 0; }
  html, body {
    width: 1200px;
    height: 724px;
    overflow: hidden;
    background: var(--backdrop);
  }
  .canvas {
    position: relative;
    width: 1200px;
    height: 724px;
  }
  .card {
    position: absolute;
    width: 540px;
    height: 310px;
    overflow: hidden;
    box-shadow: 0 6px 18px rgba(0, 0, 0, 0.25);
  }

  /* Front */
  .card-front {
    left: 50px;
    top: 70px;
    background: var(--card-white);
  }
  .card-front .brand-name {
    position: absolute;
    left: 30px;
    top: 58px;
    font-family: "Tinos", serif;
    font-weight: 400;
    font-size: 50px;
    color: var(--brand-blue);
    letter-spacing: -0.5px;
    white-space: nowrap;
  }
  .card-front .address {
    position: absolute;
    left: 32px;
    top: 138px;
    font-family: "Jost", sans-serif;
    font-size: 14px;
    color: var(--ink);
    white-space: nowrap;
  }
  .contact-list {
    position: absolute;
    left: 32px;
    top: 168px;
    list-style: none;
    font-family: "Jost", sans-serif;
    font-size: 14px;
    color: var(--ink);
    line-height: 21px;
  }
  .contact-list li { display: flex; align-items: center; gap: 6px; white-space: nowrap; }
  .contact-list svg { width: 11px; height: 11px; fill: var(--brand-blue); }
  .card-front .wave {
    position: absolute;
    left: 0;
    top: 0;
    width: 540px;
    height: 310px;
  }
  .slogan {
    position: absolute;
    right: 22px;
    top: 248px;
    font-family: "Tinos", serif;
    font-weight: 700;
    font-size: 22px;
    color: var(--slogan-orange);
    white-space: nowrap;
  }

  /* Back */
  .card-back {
    left: 610px;
    top: 340px;
    background: radial-gradient(ellipse at 55% 45%, var(--brand-sky) 0%, var(--brand-blue) 40%, var(--brand-navy) 100%);
  }
  .back-frame {
    position: absolute;
    left: 130px;
    top: 20px;
    width: 270px;
    height: 270px;
    border: 5px solid var(--faint-white);
  }
  .card-back .brand-name {
    position: absolute;
    left: 0;
    width: 100%;
    top: 108px;
    text-align: center;
    font-family: "Tinos", serif;
    font-weight: 400;
    font-size: 56px;
    color: var(--card-white);
    white-space: nowrap;
  }
  .company-name {
    position: absolute;
    left: 0;
    width: 100%;
    top: 180px;
    text-align: center;
    font-family: "Tinos", serif;
    font-weight: 700;
    font-size: 20px;
    color: rgba(120, 190, 235, 0.35);
  }
  .website {
    position: absolute;
    left: 0;
    width: 100%;
    top: 222px;
    text-align: center;
    font-family: "Tinos", serif;
    font-size: 14px;
    letter-spacing: 3px;
    color: var(--card-white);
  }
</style>
</head>
<body>
<main class="canvas">

  <section class="card card-front" aria-label="Business card front">
    <svg class="wave" viewBox="0 0 540 310" aria-hidden="true">
      <path d="M0 262 C 170 270, 340 230, 540 170 L540 186 C 340 246, 170 286, 0 280 Z" fill="var(--slogan-orange)"/>
      <path d="M0 286 C 170 292, 350 250, 540 196 L540 310 L0 310 Z" fill="var(--brand-blue)"/>
      <path d="M210 300 C 330 280, 440 235, 540 200" stroke="var(--brand-navy)" stroke-width="3" fill="none"/>
    </svg>
    <h1 class="brand-name">MoneyMendPlus</h1>
    <p class="address">30871 Calloway Ln. B-22, Houston, TX 75419</p>
    <ul class="contact-list">
      <li><svg viewBox="0 0 12 12"><path d="M3 1 L5 4 L4 5 C5 7 6 8 8 8 L9 7 L11 9 L9 11 C5 11 1 7 1 3 Z"/></svg>555-318-6207</li>
      <li><svg viewBox="0 0 12 12"><rect x="3" y="1" width="6" height="4"/><rect x="1" y="5" width="10" height="5" rx="1"/></svg>555-294-7153</li>
      <li><svg viewBox="0 0 12 12"><path d="M1 3 H11 V10 H1 Z M1 3 L6 7 L11 3" stroke="#fff" stroke-width="0.8"/></svg>info@miravelllending.example</li>
    </ul>
    <p class="slogan">Balance, Renewed!</p>
  </section>

  <section class="card card-back" aria-label="Business card back">
    <div class="back-frame"></div>
    <h2 class="brand-name">MoneyMendPlus</h2>
    <p class="company-name">Mira Vell Lending</p>
    <p class="website">www.miravelllending.example</p>
  </section>

</main>
</body>
</html>
```